QuarryDesk Company Powerpoint Template

I would like to create a branded PowerPoint temple that my company can use for all presentations. our website is www.quarrydesk.example. The company is a software provider for the auto recycling industry (junk yards). Our customers use our software to pull, process, and deliver orders to auto body shops and mechanic shops.
Pages that would be helpful:
Title Page
Content slide
Content slide with image
Workflow/flowchart slide
Image only slide
Final slide

Target Market(s)

Automotive Recycling

Industry/Entity Type

Automotive recycling software

Font styles to use
Sans Serif

Colors
0054AA
0677BA
7BADD7
CADEEF
E8F1F8
FFF300
FFF600
FEFA6F
FFFEC7
FFFEE8

Requirements
Must have
• similarities in other branded items like our website. Title Page, Content slide, Content slide with image, Workflow/flowchart slide, Image only slide, Final slide
Nice to have
• Simple clean design would be preferential

```html
<!DOCTYPE html>
<html lang="en">
<head>
<meta charset="utf-8">
<title>QuarryDesk Presentation Template</title>
<link href="https://fonts.googleapis.com/css2?family=Roboto:wght@400;500;700;900&display=swap" rel="stylesheet">
<style>
:root{
  --brand:#0054AA;
  --brand-deep:#0a4aa0;
  --brand-mid:#0677BA;
  --brand-soft:#7BADD7;
  --brand-pale:#E8F1F8;
  --page:#f2f2f2;
  --ink:#1f2a36;
  --muted:#7a7f86;
  --rule:#dcdfe3;
  --white:#ffffff;
}
*{margin:0;padding:0;box-sizing:border-box}
html,body{width:1200px;height:4898px;overflow:hidden}
body{background:var(--page);font-family:"Roboto",Arial,sans-serif;color:var(--ink);position:relative}
.slide{position:absolute;left:51px;width:1097px;height:618px;background:var(--white);overflow:hidden;box-shadow:0 1px 4px rgba(0,0,0,.12)}
.wordmark{font-family:"Roboto",Arial,sans-serif;font-weight:900;color:var(--brand);letter-spacing:-.5px;white-space:nowrap}
.header-rule{position:absolute;left:15px;top:21px;width:44px;height:3px;background:var(--brand)}
.slide-title{position:absolute;left:15px;top:31px;font-size:27px;font-weight:500;letter-spacing:.3px;color:var(--ink)}
.header-mark{position:absolute;right:16px;top:26px;font-size:26px}
.copyright{position:absolute;left:17px;top:589px;font-size:11px;color:#333}
.page-corner{position:absolute;right:0;bottom:0;width:80px;height:72px}
.page-no{position:absolute;right:14px;bottom:12px;font-size:20px;font-weight:700;color:var(--white)}

/* title */
.title-photo{position:absolute;inset:0;background:linear-gradient(100deg,#e4eee0 0%,#cfe0c6 30%,#e6efe6 60%,#f3f6f2 100%)}
.title-mark{position:absolute;left:520px;top:210px;font-size:86px;color:#123d78}

/* agenda */
.agenda-band{position:absolute;left:0;top:0;width:238px;height:618px;background:var(--brand)}
.agenda-note{position:absolute;left:19px;top:32px;font-size:11px;color:var(--white)}
.agenda-title{position:absolute;left:19px;top:290px;font-size:36px;font-weight:500;color:var(--white)}
.agenda-mark{position:absolute;left:19px;top:565px;font-size:30px;color:var(--white)}
.agenda-photo{position:absolute;left:238px;top:0;width:325px;height:618px;background:radial-gradient(circle at 50% 45%,#6fa6a8 0 18%,#3f8a34 30%,#2f6e22 70%,#245a1a 100%)}
.agenda-list{position:absolute;left:0;top:0;width:1097px;height:618px;list-style:none}
.agenda-item{position:absolute;left:640px;width:422px;height:68px;border-bottom:1px solid var(--rule);font-size:18px;font-weight:500;color:#333;letter-spacing:.3px;display:flex;align-items:center}
.agenda-tab{position:absolute;left:-82px;top:50%;margin-top:-22px;width:54px;height:44px;background:var(--brand);border-radius:0 22px 22px 0;display:flex;align-items:center;justify-content:center}

/* about */
.about-mark{position:absolute;left:82px;top:275px;width:430px;text-align:center;font-size:78px}
.about-copy{position:absolute;left:560px;top:158px;width:466px;font-size:11.6px;line-height:24px;color:#6b6f75}

/* flowchart */
.flow-list{list-style:none}
.flow-step{position:absolute;left:74px;width:480px;display:flex;align-items:center;font-size:14.5px;line-height:21px;color:#555}
.flow-num{flex:0 0 31px;height:31px;border-radius:50%;border:1px solid #c9ced4;display:flex;align-items:center;justify-content:center;font-size:15px;font-weight:700;color:var(--brand);margin-right:28px}
.flow-diagram{position:absolute;left:580px;top:90px;width:460px;height:500px}
.flow-center{position:absolute;left:660px;top:322px;width:300px;text-align:center;font-size:44px}

/* timeline */
.timeline{position:absolute;left:0;top:0;width:1097px;height:618px}
.tl-caption{position:absolute;width:130px;text-align:center;font-size:10px;line-height:16px;color:#777}

/* gallery */
.tile{position:absolute;width:260px;height:218px}

/* final */
.final{background:var(--brand-deep)}
.final-mark{position:absolute;left:34px;top:285px;font-size:74px;color:var(--white)}
.final-divider{position:absolute;left:617px;top:170px;width:1px;height:280px;background:rgba(255,255,255,.7)}
.final-title{position:absolute;left:704px;top:182px;font-size:37px;font-weight:500;color:var(--white);letter-spacing:.5px}
.contact-list{list-style:none}
.contact{position:absolute;left:716px;display:flex;align-items:flex-start;font-size:17px;line-height:21px;color:var(--white)}
.contact svg{flex:0 0 18px;margin-right:18px;margin-top:1px}
</style>
</head>
<body>

<!-- Title -->
<section class="slide" style="top:70px">
  <div class="title-photo" role="img" aria-label="Green recycling arrows and a fresh leaf on a soft blurred green background"></div>
  <div class="wordmark title-mark">QuarryDesk</div>
</section>

<!-- Agenda -->
<section class="slide" style="top:768px">
  <div class="agenda-band">
    <p class="agenda-note">Add Your Text Here</p>
    <h2 class="agenda-title">AGENDA</h2>
    <div class="wordmark agenda-mark">QuarryDesk</div>
  </div>
  <div class="agenda-photo" role="img" aria-label="Aerial view of a dense green forest with a recycling-arrow shaped clearing"></div>
  <ul class="agenda-list">
    <li class="agenda-item" style="top:108px"><span class="agenda-tab"><svg width="20" height="20" viewBox="0 0 20 20"><circle cx="10" cy="10" r="8" fill="none" stroke="#fff" stroke-width="1.3"/><path d="M8.5 6.5 12 10 8.5 13.5" fill="none" stroke="#fff" stroke-width="1.4"/></svg></span>INTRODUCTION</li>
    <li class="agenda-item" style="top:176px"><span class="agenda-tab"><svg width="20" height="20" viewBox="0 0 20 20"><circle cx="10" cy="10" r="8" fill="none" stroke="#fff" stroke-width="1.3"/><path d="M8.5 6.5 12 10 8.5 13.5" fill="none" stroke="#fff" stroke-width="1.4"/></svg></span>ABOUT US</li>
    <li class="agenda-item" style="top:244px"><span class="agenda-tab"><svg width="20" height="20" viewBox="0 0 20 20"><circle cx="10" cy="10" r="8" fill="none" stroke="#fff" stroke-width="1.3"/><path d="M8.5 6.5 12 10 8.5 13.5" fill="none" stroke="#fff" stroke-width="1.4"/></svg></span>WORKFLOW/FLOWCHART</li>
    <li class="agenda-item" style="top:312px"><span class="agenda-tab"><svg width="20" height="20" viewBox="0 0 20 20"><circle cx="10" cy="10" r="8" fill="none" stroke="#fff" stroke-width="1.3"/><path d="M8.5 6.5 12 10 8.5 13.5" fill="none" stroke="#fff" stroke-width="1.4"/></svg></span>TIMELINE</li>
    <li class="agenda-item" style="top:380px"><span class="agenda-tab"><svg width="20" height="20" viewBox="0 0 20 20"><circle cx="10" cy="10" r="8" fill="none" stroke="#fff" stroke-width="1.3"/><path d="M8.5 6.5 12 10 8.5 13.5" fill="none" stroke="#fff" stroke-width="1.4"/></svg></span>IMAGE</li>
    <li class="agenda-item" style="top:448px"><span class="agenda-tab"><svg width="20" height="20" viewBox="0 0 20 20"><circle cx="10" cy="10" r="8" fill="none" stroke="#fff" stroke-width="1.3"/><path d="M8.5 6.5 12 10 8.5 13.5" fill="none" stroke="#fff" stroke-width="1.4"/></svg></span>FINAL</li>
  </ul>
</section>

<!-- About -->
<section class="slide" style="top:1460px">
  <div class="header-rule"></div>
  <h2 class="slide-title">ABOUT US</h2>
  <div class="wordmark header-mark">QuarryDesk</div>
  <div class="wordmark about-mark">QuarryDesk</div>
  <p class="about-copy">Sed ut perspiciatis unde omnis iste natus error sit voluptatem accusantium doloremque laudantium, totam rem aperiam, eaque ipsa quae ab illo inventore veritatis et quasi arc hitecto beatae vitae dicta sunt explicabo. Nemo enim ipsam voluptatem quia voluptas sit aspernatur aut odit aut fugit, sed quia consequuntur magni dolores eos qui ratione vol uptatem sequi nesciunt. Neque porro quisquam est, qui dolorem ipsum quia dolor sit amet, consectetur, adipisci velit, sed quia non numquam eius modi tempora incidunt ut labore et dolore magnam aliquam quaerat voluptatem. Ut enim ad minima veniam, quis nostrum exercitationem ullam corporis suscipit laboriosam, nisi ut aliquid ex ea commodi consequatur. Quis autem vel eum iure reprehenderit qui in ea voluptate velit esse vel illum qui dolorem eum fugiat quo voluptas nulla pariatur. Sed ut perspiciatis unde omnis iste natus error sit voluptatem accusantium doloremque laudantium, totam rem veritatis et quasi architecto beatae vitae dic omnis iste natus error sit voluptatem accusantium dolore mque laudantium, totam ta accusantium dolore mque laudantium, totam sunt explicabo.</p>
  <p class="copyright">© Copyright 2022 QuarryDesk.All rights reserved.</p>
  <svg class="page-corner" viewBox="0 0 80 72"><path d="M80 0V72H0Z" fill="var(--brand)"/></svg>
  <span class="page-no">03</span>
</section>

<!-- Flowchart -->
<section class="slide" style="top:2152px">
  <div class="header-rule"></div>
  <h2 class="slide-title">FLOWCHART</h2>
  <div class="wordmark header-mark">QuarryDesk</div>
  <ol class="flow-list">
    <li class="flow-step" style="top:150px"><span class="flow-num">01</span>Sed ut perspiciatis unde omnis iste natus error sit volup tatem accusantium doloremque laudantium,</li>
    <li class="flow-step" style="top:230px"><span class="flow-num">02</span>Nemo enim ipsam voluptatem quia voluptas sit aspernatur</li>
    <li class="flow-step" style="top:298px"><span class="flow-num">03</span>Nemo enim ipsam voluptatem quia voluptas sit aspernatur aut odit aut fugit</li>
    <li class="flow-step" style="top:382px"><span class="flow-num">04</span>Sed ut perspiciatis unde omnis iste natus</li>
    <li class="flow-step" style="top:456px"><span class="flow-num">05</span>Sed ut perspiciatis unde omnis iste natus</li>
  </ol>
  <svg class="flow-diagram" viewBox="580 90 460 500" fill="none" stroke="var(--brand)" stroke-width="2">
    <circle cx="810" cy="342" r="186" stroke="#b8bcc2" stroke-width="1.2" stroke-dasharray="4 4"/>
    <circle cx="810" cy="342" r="142" fill="#f4f5f6" stroke="none"/>
    <g>
      <circle cx="810" cy="152" r="52" fill="#fff"/>
      <path d="M788 175V152l12-8v8l12-8v8l12-8v31Z M800 163h6v6h-6Z M813 163h6v6h-6Z M818 144v-14h5v14" stroke-width="1.8"/>
      <circle cx="773" cy="114" r="15" fill="#fff"/>
    </g>
    <g>
      <circle cx="979" cy="270" r="52" fill="#fff"/>
      <path d="M964 256h30 M969 256l2 32h16l2-32 M974 252h10 M974 264v18 M984 264v18" stroke-width="1.8"/>
      <circle cx="1020" cy="232" r="15" fill="#fff"/>
    </g>
    <g>
      <circle cx="947" cy="475" r="52" fill="#fff"/>
      <path d="M930 478a18 18 0 0 1 30-14 M964 472a18 18 0 0 1-30 14 M956 458l4 6-7 2 M938 492l-4-6 7-2" stroke-width="1.8"/>
      <circle cx="988" cy="437" r="15" fill="#fff"/>
    </g>
    <g>
      <circle cx="673" cy="467" r="52" fill="#fff"/>
      <path d="M666 448l-12 20h12 M680 448l12 20h-8 M662 486h22l-6-10" stroke-width="1.8"/>
      <circle cx="630" cy="430" r="15" fill="#fff"/>
    </g>
    <g>
      <circle cx="637" cy="258" r="52" fill="#fff"/>
      <path d="M622 240h14v14h-14Z M629 254v10 M620 264h20l4 16h-28Z M646 270a8 8 0 1 0 0.1 0" stroke-width="1.8"/>
      <circle cx="596" cy="222" r="15" fill="#fff"/>
    </g>
    <g fill="var(--brand)" stroke="none" font-family="Roboto, Arial, sans-serif" font-size="12" font-weight="700" text-anchor="middle">
      <text x="773" y="118">01</text>
      <text x="1020" y="236">02</text>
      <text x="988" y="441">03</text>
      <text x="630" y="434">04</text>
      <text x="596" y="226">05</text>
    </g>
  </svg>
  <div class="wordmark flow-center">QuarryDesk</div>
  <p class="copyright">© Copyright 2022 QuarryDesk.All rights reserved.</p>
  <svg class="page-corner" viewBox="0 0 80 72"><path d="M80 0V72H0Z" fill="var(--brand)"/></svg>
  <span class="page-no">04</span>
</section>

<!-- Timeline -->
<section class="slide" style="top:2838px">
  <div class="header-rule"></div>
  <h2 class="slide-title">TIMELINE</h2>
  <div class="wordmark header-mark">QuarryDesk</div>
  <svg class="timeline" viewBox="0 0 1097 618">
    <path d="M34 318 C60 370 80 384 110 384 C183 384 183 289 257 289 C330 289 330 384 403 384 C476 384 476 289 549 289 C624 289 624 384 699 384 C772 384 772 289 844 289 C915 289 915 384 985 384 C1025 384 1045 350 1060 318" fill="none" stroke="var(--brand)" stroke-width="7" stroke-linecap="round"/>
    <g fill="#fff" stroke="var(--brand)" stroke-width="2">
      <circle cx="110" cy="384" r="4"/><circle cx="257" cy="289" r="4"/><circle cx="403" cy="384" r="4"/><circle cx="549" cy="289" r="4"/><circle cx="699" cy="384" r="4"/><circle cx="844" cy="289" r="4"/><circle cx="985" cy="384" r="4"/>
    </g>
    <g fill="var(--brand)">
      <path d="M110 318c-18-14-32-26-32-42a32 32 0 0 1 64 0c0 16-14 28-32 42Z"/>
      <path d="M257 223c-18-14-32-26-32-42a32 32 0 0 1 64 0c0 16-14 28-32 42Z"/>
      <path d="M403 318c-18-14-32-26-32-42a32 32 0 0 1 64 0c0 16-14 28-32 42Z"/>
      <path d="M549 223c-18-14-32-26-32-42a32 32 0 0 1 64 0c0 16-14 28-32 42Z"/>
      <path d="M699 318c-18-14-32-26-32-42a32 32 0 0 1 64 0c0 16-14 28-32 42Z"/>
      <path d="M844 223c-18-14-32-26-32-42a32 32 0 0 1 64 0c0 16-14 28-32 42Z"/>
      <path d="M985 318c-18-14-32-26-32-42a32 32 0 0 1 64 0c0 16-14 28-32 42Z"/>
    </g>
    <g fill="#fff">
      <circle cx="110" cy="276" r="24"/><circle cx="257" cy="181" r="24"/><circle cx="403" cy="276" r="24"/><circle cx="549" cy="181" r="24"/><circle cx="699" cy="276" r="24"/><circle cx="844" cy="181" r="24"/><circle cx="985" cy="276" r="24"/>
    </g>
    <g fill="#333" font-family="Roboto, Arial, sans-serif" font-size="9.5" font-weight="700" text-anchor="middle">
      <text x="110" y="274">MAY</text><text x="110" y="286">2020</text>
      <text x="257" y="179">APRIL</text><text x="257" y="191">2020</text>
      <text x="403" y="274">SEP</text><text x="403" y="286">2019</text>
      <text x="549" y="179">MAY</text><text x="549" y="191">2019</text>
      <text x="699" y="274">MAR</text><text x="699" y="286">2019</text>
      <text x="844" y="179">JUN</text><text x="844" y="191">2018</text>
      <text x="985" y="274">MAY</text><text x="985" y="286">2022</text>
    </g>
  </svg>
  <p class="tl-caption" style="left:45px;top:438px">Sed ut perspiciatis unde omnis iste natus error sit voluptatem accusantium doloremque laudan</p>
  <p class="tl-caption" style="left:192px;top:352px">Sed ut perspiciatis unde omnis iste natus error sit voluptatem accusantium doloremque laudan</p>
  <p class="tl-caption" style="left:338px;top:438px">Sed ut perspiciatis unde omnis iste natus error sit voluptatem accusantium doloremque laudan</p>
  <p class="tl-caption" style="left:484px;top:352px">Sed ut perspiciatis unde omnis iste natus error sit voluptatem accusantium doloremque laudan</p>
  <p class="tl-caption" style="left:634px;top:438px">Sed ut perspiciatis unde omnis iste natus error sit voluptatem accusantium doloremque laudan</p>
  <p class="tl-caption" style="left:779px;top:352px">Sed ut perspiciatis unde omnis iste natus error sit voluptatem accusantium doloremque laudan</p>
  <p class="tl-caption" style="left:920px;top:438px">Sed ut perspiciatis unde omnis iste natus error sit voluptatem accusantium doloremque laudan</p>
  <p class="copyright">© Copyright 2022 QuarryDesk.All rights reserved.</p>
  <svg class="page-corner" viewBox="0 0 80 72"><path d="M80 0V72H0Z" fill="var(--brand)"/></svg>
  <span class="page-no">05</span>
</section>

<!-- Gallery -->
<section class="slide" style="top:3524px">
  <div class="header-rule"></div>
  <h2 class="slide-title">GALLERY</h2>
  <div class="wordmark header-mark">QuarryDesk</div>
  <div class="tile" style="left:15px;top:78px;background:linear-gradient(160deg,#8a9aa8,#5c6a58)" role="img" aria-label="Workers in safety vests inspecting parts at a recycling yard"></div>
  <div class="tile" style="left:284px;top:78px;background:linear-gradient(160deg,#c9d3d8,#7b8a86)" role="img" aria-label="Hand holding a plastic bottle for recycling"></div>
  <div class="tile" style="left:553px;top:78px;background:linear-gradient(160deg,#a79a86,#4f5d75)" role="img" aria-label="Worker with clipboard beside heavy machinery in a warehouse"></div>
  <div class="tile" style="left:822px;top:78px;background:linear-gradient(160deg,#9a9890,#6c6b62)" role="img" aria-label="Aerial view of a scrap recycling yard"></div>
  <div class="tile" style="left:15px;top:306px;background:linear-gradient(160deg,#b7a98e,#6f6a5c)" role="img" aria-label="Sorted bins of scrap metal parts seen from above"></div>
  <div class="tile" style="left:284px;top:306px;background:linear-gradient(160deg,#6d6d6a,#3a3a38)" role="img" aria-label="Pile of crushed metal scrap with a yellow bin"></div>
  <div class="tile" style="left:553px;top:306px;background:linear-gradient(160deg,#c9b79c,#6a5140)" role="img" aria-label="Grapple claw lifting scrap metal at sunset"></div>
  <div class="tile" style="left:822px;top:306px;background:linear-gradient(160deg,#8d8f8a,#5d6058)" role="img" aria-label="Aerial view of an industrial recycling facility"></div>
  <p class="copyright">© Copyright 2022 QuarryDesk.All rights reserved.</p>
  <svg class="page-corner" viewBox="0 0 80 72"><path d="M80 0V72H0Z" fill="var(--brand)"/></svg>
  <span class="page-no">06</span>
</section>

<!-- Final -->
<section class="slide final" style="top:4216px">
  <div class="wordmark final-mark">QuarryDesk</div>
  <div class="final-divider"></div>
  <h2 class="final-title">THANK YOU</h2>
  <ul class="contact-list">
    <li class="contact" style="top:268px"><svg width="18" height="20" viewBox="0 0 18 20"><path d="M9 1a6 6 0 0 0-6 6c0 5 6 11 6 11s6-6 6-11a6 6 0 0 0-6-6Z" fill="#fff"/><circle cx="9" cy="7" r="2.2" fill="var(--brand-deep)"/></svg><span>48 Harbor Lane, Millbrook<br>OH 40000</span></li>
    <li class="contact" style="top:331px"><svg width="18" height="18" viewBox="0 0 18 18"><path d="M4 1l3 3-2 2.5a10 10 0 0 0 6.5 6.5L14 11l3 3-2.5 3C7 16.5 1.5 11 1 3.5Z" fill="#fff"/></svg><span>555-014-2277</span></li>
    <li class="contact" style="top:378px"><svg width="18" height="18" viewBox="0 0 18 18" fill="none" stroke="#fff" stroke-width="1.6"><circle cx="9" cy="9" r="7.5"/><ellipse cx="9" cy="9" rx="3.2" ry="7.5"/><path d="M1.5 9h15"/></svg><span>www.quarrydesk.example</span></li>
    <li class="contact" style="top:426px"><svg width="18" height="16" viewBox="0 0 18 16"><rect x="1" y="2" width="16" height="12" rx="1" fill="#fff"/><path d="M1.5 3 9 9l7.5-6" fill="none" stroke="var(--brand-deep)" stroke-width="1.4"/></svg><span>support@quarrydesk.example</span></li>
  </ul>
</section>

</body>
</html>
```